Stationery for a private security company, "Brenmoor Security Services Ltd."

Needed is a stationery design for a private security company. The designs must show professionalism and that our company mean nothing but business. Watermark of the company logo on the letterhead page is also a must. The final design must represent innovation and professionalism. It would be great if designers could integrate the colours black and silver onto the cards and letterheads..

Thank you

```html
<!DOCTYPE html>
<html lang="en">
<head>
<meta charset="utf-8">
<title>Brenmoor Security Services Ltd. – Business Cards</title>
<link rel="stylesheet" href="https://fonts.googleapis.com/css2?family=Cinzel:wght@500;700&family=Questrial&display=swap">
<style>
  :root {
    --backdrop: #5c5d5f;
    --card-dark: #1f2024;
    --card-dark-edge: #2b2c31;
    --card-light: #f4f4f4;
    --ink: #111113;
    --silver: #c9cacd;
    --silver-light: #e8e8ea;
    --silver-soft: #9a9ba0;
    --band-stripe: #b4b5b8;
    --band-text: #cfd0d3;
  }
  * { box-sizing: border-box; margin: 0; padding: 0; }
  html, body {
    width: 1200px; height: 1000px; overflow: hidden;
    background: var(--backdrop);
    font-family: "Questrial", "Century Gothic", sans-serif;
  }
  .canvas { position: relative; width: 1200px; height: 1000px; }

  .card {
    position: absolute;
    width: 528px; height: 304px;
    border-radius: 14px;
    overflow: hidden;
  }
  .card--front {
    left: 365px; top: 165px;
    background: linear-gradient(160deg, var(--card-dark-edge), var(--card-dark) 60%);
    color: var(--silver-light);
  }
  .card--back {
    left: 266px; top: 550px;
    background: var(--card-light);
    color: var(--ink);
  }

  .brand {
    position: absolute; left: 0; right: 0;
    text-align: center;
    font-family: "Cinzel", "Times New Roman", serif;
  }
  .brand__mark {
    display: block; margin: 0 auto 48px;
    width: 40px; height: 40px; border-radius: 50%;
    border: 2px solid currentColor;
  }
  .brand__name {
    display: block; font-size: 38px; line-height: 1;
    letter-spacing: 0.06em;
  }
  .brand__sub {
    display: block; font-size: 17px; line-height: 1; margin-top: 6px;
    letter-spacing: 0.02em;
  }
  .card--front .brand { top: 66px; font-weight: 500; }
  .card--back .brand { top: 48px; font-weight: 700; }

  .tagline {
    position: absolute; left: 0; right: 0; top: 248px;
    text-align: center; font-size: 13px; letter-spacing: 0.03em;
    color: var(--silver);
  }

  .contact-band {
    position: absolute; left: 0; right: 0; top: 238px; bottom: 0;
    background: var(--card-dark);
    border-top: 5px solid var(--band-stripe);
    display: flex; align-items: center;
    padding: 0 0 0 43px;
    color: var(--band-text);
    font-size: 11px; line-height: 17px;
  }
  .contact-band__col { height: 36px; }
  .contact-band__col--address { width: 163px; }
  .contact-band__col--phone { width: 136px; padding-left: 22px; }
  .contact-band__col--web { padding-left: 22px; }
  .contact-band__divider {
    width: 1px; height: 26px; background: var(--silver-soft);
  }
  .contact-line { display: flex; align-items: center; gap: 7px; white-space: nowrap; }
  .contact-line svg { width: 11px; height: 11px; flex: none; }
</style>
</head>
<body>
<main class="canvas">

  <section class="card card--front" aria-label="Card front">
    <div class="brand">
      <span class="brand__mark" aria-hidden="true"></span>
      <span class="brand__name">Brenmoor</span>
      <span class="brand__sub">Security Services Ltd.</span>
    </div>
    <p class="tagline">STEADFAST IN EVERY DETAIL</p>
  </section>

  <section class="card card--back" aria-label="Card back">
    <div class="brand">
      <span class="brand__mark" aria-hidden="true"></span>
      <span class="brand__name">Brenmoor</span>
      <span class="brand__sub">Security Services Ltd.</span>
    </div>

    <footer class="contact-band">
      <div class="contact-band__col contact-band__col--address">
        <p>Unit 7 Ashgrove Trade Park</p>
        <p>Halden Road, London</p>
      </div>
      <span class="contact-band__divider"></span>
      <div class="contact-band__col contact-band__col--phone">
        <p class="contact-line">
          <svg viewBox="0 0 12 12" aria-hidden="true"><circle cx="6" cy="6" r="5.3" fill="none" stroke="currentColor" stroke-width="0.9"/><path d="M4 3.2l1 1.3-.6.7c.4.9 1 1.5 1.9 1.9l.7-.6 1.3 1-.5.9c-2 0-4.2-2.2-4.3-4.3z" fill="currentColor"/></svg>
          0700-900-118
        </p>
        <p class="contact-line">
          <svg viewBox="0 0 12 12" aria-hidden="true"><circle cx="6" cy="6" r="5.3" fill="none" stroke="currentColor" stroke-width="0.9"/><rect x="3.5" y="5" width="5" height="3" fill="currentColor"/><rect x="4.3" y="3.3" width="3.4" height="1.4" fill="currentColor"/></svg>
          0700 900 119
        </p>
      </div>
      <span class="contact-band__divider"></span>
      <div class="contact-band__col contact-band__col--web">
        <p class="contact-line">
          <svg viewBox="0 0 12 12" aria-hidden="true"><circle cx="6" cy="6" r="5.3" fill="none" stroke="currentColor" stroke-width="0.9"/><rect x="3.4" y="4.2" width="5.2" height="3.6" fill="none" stroke="currentColor" stroke-width="0.8"/><path d="M3.4 4.2L6 6.3l2.6-2.1" fill="none" stroke="currentColor" stroke-width="0.8"/></svg>
          info@brenmoor.example
        </p>
        <p class="contact-line">
          <svg viewBox="0 0 12 12" aria-hidden="true"><circle cx="6" cy="6" r="5.3" fill="none" stroke="currentColor" stroke-width="0.9"/><ellipse cx="6" cy="6" rx="2.2" ry="5.3" fill="none" stroke="currentColor" stroke-width="0.8"/><path d="M0.8 6h10.4M1.6 3.5h8.8M1.6 8.5h8.8" stroke="currentColor" stroke-width="0.7"/></svg>
          www.brenmoor.example
        </p>
      </div>
    </footer>
  </section>

</main>
</body>
</html>
```